Corvane Paintless Dent Removal

Our company works on vehicles removing dents using a highly skilled trade which the metal is massaged out with special tools without disturbing the original paint, hence paintless dent removal. Besides keeping the paint and metal original its also very environmentally friendly since no paint or toxic fillers are used. Also we we are one of the most experienced companies in the business with 25 years

Target Market(s)

Retail Automobile consumers, Auto Dealerships and Auto Body Shops

Industry/Entity Type

Auto Repair

Contact Information for Business Card

Dale Hollister
PO Box 518 Brookmere, NY 11962
631-555-0148
corvanepdr@mailbox-example.com
website corvanepdr.example
youtube corvane paintless dent removal
25 years of experience removing Dents, Dings and Hail Damage

Font styles to use
Serif
Sans Serif

Colors

Designer to choose colors to be used in the design.

Requirements
Must have
• I do like things that are simple but classy and somewhat bold, also I like my logo so that should be somewhat important

```html
<!DOCTYPE html>
<html lang="en">
<head>
<meta charset="utf-8">
<title>Corvane Paintless Dent Removal – Business Card</title>
<link rel="stylesheet" href="https://fonts.googleapis.com/css2?family=Roboto:wght@400;500&family=Roboto+Condensed:wght@700&display=swap">
<style>
  :root {
    --backdrop: #2b2b2b;
    --card-white: #f3f3f3;
    --navy: #12284c;
    --green: #7dc618;
    --text-grey: #444;
    --rule-grey: #7a7a7a;
    --gold: #d9a441;
    --gold-dark: #1a1a1a;
    --white: #ffffff;
  }
  html, body { margin: 0; padding: 0; overflow: hidden; }
  body {
    width: 1200px; height: 960px;
    background: var(--backdrop);
    position: relative;
    font-family: "Roboto", Arial, sans-serif;
  }
  .card { position: absolute; width: 600px; height: 342px; overflow: hidden; }
  .card-front { left: 314px; top: 113px; background: var(--card-white); }
  .card-back { left: 311px; top: 472px; background: var(--navy); }

  .brand-name {
    position: absolute;
    font-family: "Roboto Condensed", Arial, sans-serif;
    font-weight: 700;
    text-align: center;
    line-height: 1;
  }
  .brand-name .brand-word { display: block; font-size: 36px; letter-spacing: 0.5px; }
  .brand-name .brand-tag { display: block; font-size: 16px; margin-top: 3px; }
  .card-front .brand-name { left: 285px; top: 56px; width: 280px; color: var(--navy); }
  .card-back .brand-name { left: 150px; top: 146px; width: 300px; color: var(--white); }
  .card-back .brand-name .brand-word { font-size: 42px; }
  .card-back .brand-name .brand-tag { font-size: 18px; }

  .holder-name {
    position: absolute; left: 37px; top: 196px; margin: 0;
    font-family: "Roboto Condensed", Arial, sans-serif;
    font-weight: 700; font-size: 22px; color: var(--navy);
    text-transform: uppercase;
  }
  .name-rule {
    position: absolute; left: 39px; top: 228px; width: 525px; height: 1.5px;
    background: var(--rule-grey);
  }
  .contact-list { position: absolute; left: 36px; top: 241px; margin: 0; padding: 0; list-style: none; }
  .contact-list li {
    display: flex; align-items: center; gap: 8px;
    font-size: 14px; color: var(--text-grey); height: 19px;
  }
  .contact-list svg { width: 14px; height: 14px; flex: none; }
  .postal-address {
    position: absolute; right: 35px; top: 261px; margin: 0;
    font-style: normal; font-size: 14px; line-height: 19px;
    color: var(--text-grey); text-align: right;
  }
  .footer-bands { position: absolute; left: 0; bottom: 0; width: 600px; height: 32px; }
  .website {
    position: absolute; right: 30px; bottom: 9px;
    font-size: 14px; letter-spacing: 2.6px; color: var(--white);
  }

  .experience-seal { position: absolute; left: 18px; top: 23px; width: 76px; height: 76px; }
</style>
</head>
<body>

<section class="card card-front" aria-label="Business card front">
  <div class="brand-name">
    <span class="brand-word">CORVANE</span>
    <span class="brand-tag">Paintless Dent Removal</span>
  </div>

  <h1 class="holder-name">Dale Hollister</h1>
  <div class="name-rule"></div>

  <ul class="contact-list">
    <li>
      <svg viewBox="0 0 24 24" aria-hidden="true"><path fill="#12284c" d="M6.6 10.8a15.1 15.1 0 0 0 6.6 6.6l2.2-2.2c.3-.3.7-.4 1-.2 1.1.4 2.3.6 3.6.6.6 0 1 .4 1 1V20c0 .6-.4 1-1 1A17 17 0 0 1 3 4c0-.6.4-1 1-1h3.5c.6 0 1 .4 1 1 0 1.3.2 2.5.6 3.6.1.3 0 .7-.2 1z"/></svg>
      <span>631-555-0148</span>
    </li>
    <li>
      <svg viewBox="0 0 24 24" aria-hidden="true"><path fill="#12284c" d="M2 5h20v14H2z"/><path fill="none" stroke="#f3f3f3" stroke-width="1.8" d="M2.5 5.5 12 13l9.5-7.5"/></svg>
      <span>corvanepdr@mailbox-example.com</span>
    </li>
    <li>
      <svg viewBox="0 0 24 24" aria-hidden="true"><rect x="3" y="5" width="18" height="14" rx="3" fill="#12284c"/></svg>
      <span>corvane paintless dent removal</span>
    </li>
  </ul>

  <address class="postal-address">PO Box 518<br>Brookmere, NY 11962</address>

  <svg class="footer-bands" viewBox="0 0 600 32" aria-hidden="true">
    <polygon points="0,8 345,8 333,22 0,22" fill="var(--green)"/>
    <polygon points="0,22 333,22 328,27 0,27" fill="var(--navy)"/>
    <polygon points="350,0 600,0 600,32 322,32" fill="var(--navy)"/>
  </svg>
  <span class="website">www.corvanepdr.example</span>
</section>

<section class="card card-back" aria-label="Business card back">
  <svg class="experience-seal" viewBox="0 0 76 76" role="img" aria-label="25 years of experience seal">
    <circle cx="38" cy="38" r="37" fill="var(--gold)"/>
    <circle cx="38" cy="38" r="27" fill="var(--gold-dark)"/>
    <circle cx="38" cy="38" r="24" fill="none" stroke="var(--gold)" stroke-width="1"/>
    <text x="38" y="42" text-anchor="middle" font-family="Roboto Condensed, Arial, sans-serif" font-weight="700" font-size="22" fill="var(--gold)">25</text>
    <text x="38" y="53" text-anchor="middle" font-family="Roboto Condensed, Arial, sans-serif" font-weight="700" font-size="9" fill="var(--gold)">YEARS</text>
  </svg>

  <div class="brand-name">
    <span class="brand-word">CORVANE</span>
    <span class="brand-tag">Paintless Dent Removal</span>
  </div>
</section>

</body>
</html>
```